5 website banners (slides show)

We need 5 website sliding banners created for a website all about internet safety. The topics for each banner are:

Cyberbullying
Fraud
seniors
social networking

Sizes: 953 pixels x 281 pixels

I have stock images to use or feel free to use your own or one I can purchase from pixelharbor.example.

Industry/Entity Type

Internet

```html
<!DOCTYPE html>
<html lang="en">
<head>
<meta charset="utf-8">
<title>NetGuard – Online Safety and Security</title>
<link rel="stylesheet" href="https://fonts.googleapis.com/css2?family=Ubuntu:wght@400;500;700&family=Fredoka:wght@600&family=Arimo:wght@400;700&display=swap">
<style>
  :root {
    --pink: #ff0a8c;
    --pink-deep: #e4007c;
    --pink-soft: #ff4fae;
    --green: #5cc80e;
    --green-dark: #45a808;
    --green-light: #74d61e;
    --text-muted: #7f929c;
    --edit: #c36ad0;
    --white: #ffffff;
    --field: #f4f6f8;
    --square: #26415e;
  }
  * { box-sizing: border-box; margin: 0; padding: 0; }
  html, body { width: 1200px; height: 1158px; overflow: hidden; background: var(--white); }
  body { position: relative; font-family: "Arimo", Arial, sans-serif; }

  .topbar { position: absolute; left: 42px; top: 29px; width: 749px; height: 39px; background: var(--pink); border-radius: 5px 0 0 5px; }
  .topbar a { position: absolute; top: 10px; color: var(--white); font-size: 15px; text-decoration: none; white-space: nowrap; }
  .social-square { position: absolute; left: 715px; top: 5px; width: 29px; height: 29px; background: var(--square); border-radius: 2px; }
  .search { position: absolute; left: 791px; top: 29px; width: 363px; height: 39px; background: var(--field); border: 1px solid #e6eaee; border-radius: 0 5px 5px 0; }
  .search span { position: absolute; left: 12px; top: 10px; color: #9aa5ad; font-size: 14px; }
  .search-btn { position: absolute; right: 3px; top: 3px; width: 32px; height: 31px; background: var(--pink); border-radius: 4px; }

  .brand-mark { position: absolute; left: 62px; top: 87px; width: 118px; height: 118px; border-radius: 50%; background: var(--pink); }
  .brand-name { position: absolute; left: 194px; top: 104px; font-family: "Ubuntu", sans-serif; font-weight: 500; font-size: 62px; line-height: 1; color: var(--pink); white-space: nowrap; }
  .brand-tagline { position: absolute; left: 197px; top: 168px; font-family: "Ubuntu", sans-serif; font-size: 16.5px; color: var(--green-dark); white-space: nowrap; }

  .report { position: absolute; left: 738px; top: 95px; width: 416px; height: 112px; background: var(--green-light); border-radius: 5px; }
  .report::before { content: ""; position: absolute; inset: 8px; border: 1px dashed rgba(255,255,255,.7); }
  .report span { position: absolute; font-family: "Ubuntu", sans-serif; color: var(--white); white-space: nowrap; }
  .report .r1 { left: 20px; top: 15px; font-weight: 700; font-size: 25px; }
  .report .r2 { left: 215px; top: 46px; font-weight: 500; font-size: 16px; }
  .report .r3 { left: 16px; top: 63px; font-weight: 700; font-size: 28px; }
  .report .badge { position: absolute; right: 14px; top: 8px; width: 82px; height: 96px; }

  .mainnav { position: absolute; left: 42px; top: 229px; width: 1112px; height: 78px; background: var(--green); border-radius: 6px; overflow: hidden; }
  .mainnav::after { content: ""; position: absolute; left: 0; bottom: 0; width: 100%; height: 13px; background: var(--green-light); }
  .mainnav ul { list-style: none; display: flex; height: 64px; }
  .mainnav li { flex: none; font-family: "Ubuntu", sans-serif; font-size: 18.5px; color: var(--white); line-height: 64px; text-align: center; white-space: nowrap; border-right: 1px solid rgba(255,255,255,.35); }
  .mainnav li.current { background: var(--green-dark); }

  .hero { position: absolute; left: 42px; top: 320px; width: 1117px; height: 328px; background: var(--pink); border-radius: 5px; overflow: hidden; }
  .hero-ghost { position: absolute; left: 440px; top: -40px; font-family: "Fredoka", sans-serif; font-weight: 600; font-size: 400px; line-height: 1; color: var(--pink-soft); opacity: .45; white-space: nowrap; }
  .hero-photo { position: absolute; left: -60px; top: -40px; width: 480px; height: 420px; border-radius: 50%; border: 14px solid var(--green); background: linear-gradient(135deg, #e8dccd, #c9b59e 55%, #6e6e70); }
  .hero-mascot { position: absolute; left: 410px; top: 88px; width: 200px; height: 240px; border-radius: 45% 45% 10px 10px; background: linear-gradient(180deg, #a6e23a, #46a62a); }
  .hero-title { position: absolute; left: 656px; top: 104px; font-family: "Fredoka", sans-serif; font-weight: 600; font-size: 88px; color: var(--white); letter-spacing: 1px; white-space: nowrap; }

  .issues { position: absolute; left: 42px; top: 662px; width: 258px; height: 520px; background: var(--green); border-radius: 6px; }
  .issues::before { content: ""; position: absolute; left: 12px; top: 12px; right: 12px; bottom: 12px; border: 1px dashed rgba(255,255,255,.8); border-radius: 6px; }
  .issues h2 { position: absolute; left: 25px; top: 34px; font-family: "Ubuntu", sans-serif; font-weight: 500; font-size: 17.5px; color: var(--white); white-space: nowrap; }
  .issues ul { position: absolute; left: 31px; top: 72px; list-style: none; }
  .issues li { font-size: 14.5px; color: var(--white); height: 29.3px; white-space: nowrap; }

  .content { position: absolute; left: 316px; top: 662px; width: 838px; height: 520px; background: var(--white); box-shadow: 4px 0 5px rgba(0,0,0,.12); }
  .content h1 { position: absolute; left: 19px; top: 22px; font-family: "Ubuntu", sans-serif; font-weight: 500; font-size: 32px; color: var(--pink); }
  .edit { position: absolute; left: 19px; top: 65px; font-size: 14px; color: var(--edit); }
  .edit::before { content: ""; display: inline-block; width: 4px; height: 4px; background: #999; margin-right: 12px; vertical-align: middle; }
  .content p { position: absolute; left: 19px; width: 800px; font-size: 14.5px; line-height: 20px; color: var(--text-muted); }

  .audience { position: absolute; top: 994px; width: 234px; }
  .audience h3 { font-family: "Ubuntu", sans-serif; font-weight: 500; font-size: 17.5px; color: var(--pink); margin-bottom: 6px; }
  .audience .thumb { width: 234px; height: 150px; }
</style>
</head>
<body>
  <header>
    <nav class="topbar">
      <a style="left:17px">Home</a>
      <a style="left:86px">FAQs</a>
      <a style="left:151px">Contact</a>
      <span class="social-square"></span>
    </nav>
    <div class="search">
      <span>Search...</span>
      <div class="search-btn">
        <svg width="32" height="31" viewBox="0 0 32 31"><circle cx="14" cy="13" r="7" fill="none" stroke="#fff" stroke-width="3.5"/><line x1="19" y1="18" x2="25" y2="24" stroke="#fff" stroke-width="4" stroke-linecap="round"/></svg>
      </div>
    </div>

    <div class="brand-mark"></div>
    <div class="brand-name">NETGUARD</div>
    <div class="brand-tagline">BERMUDA ONLINE SAFETY AND SECURITY</div>

    <div class="report">
      <span class="r1">REPORT A CYBERCRIME</span>
      <span class="r2">CLICK HERE</span>
      <span class="r3">or call 1-555-010-2040</span>
      <svg class="badge" viewBox="0 0 82 96"><path d="M41 2 L78 14 V48 C78 72 60 86 41 94 C22 86 4 72 4 48 V14 Z" fill="#2f6fb0" stroke="#c9d3dc" stroke-width="4"/></svg>
    </div>

    <nav class="mainnav">
      <ul>
        <li class="current" style="width:94px">HOME</li>
        <li style="width:101px">ABOUT</li>
        <li style="width:158px">FOR PARENTS</li>
        <li style="width:137px">FOR TEENS</li>
        <li style="width:155px">FOR TWEENS</li>
        <li style="width:120px">FOR KIDS</li>
        <li style="width:170px">FOR TEACHERS</li>
        <li style="width:143px">RESOURCES</li>
      </ul>
    </nav>
  </header>

  <section class="hero">
    <div class="hero-ghost">SEN</div>
    <div class="hero-photo" role="img" aria-label="Photo of a grandfather and a small child laughing at a laptop"></div>
    <div class="hero-mascot" role="img" aria-label="Cartoon green frog mascot giving an OK sign"></div>
    <div class="hero-title">SENIORS</div>
  </section>

  <aside class="issues">
    <h2>CHOOSE AN ISSUE</h2>
    <ul>
      <li>Cyberbullying</li>
      <li>Sexting</li>
      <li>Internet Safety</li>
      <li>Fraud</li>
      <li>Mobile Devices</li>
      <li>Gangs</li>
      <li>Blogging</li>
      <li>Predators</li>
      <li>Copywriting</li>
      <li>Social Networking</li>
      <li>Gaming</li>
      <li>eMailing, Chat Rooms</li>
      <li>File Sharing</li>
      <li>Identity Theft</li>
    </ul>
  </aside>

  <main class="content">
    <h1>WELCOME</h1>
    <div class="edit">Edit</div>
    <p style="top:114px">Welcome to NetGuard, Bermuda’s source of information on internet safety, brought to you by the Ministry of Digital Affairs. Our aim is to provide practical tips, resources and contact information to help parents, children and educators to use the Internet safely and be on guard against online predators and other inappropriate online content.</p>
    <p style="top:195px">By knowing the dangers and how to avoid them, you can take advantage of all the positive aspects of the Internet while avoiding most of its pitfalls.</p>
    <p style="top:256px">The Ministry of Digital Affairs partners with the Island Constabulary, Northgate Software, Pip’s Planet and a number of other organizations locally and internationally to bring innovative and media rich educational tools to Bermuda</p>
  </main>

  <section class="audience" style="left:323px">
    <h3>KIDS</h3>
    <div class="thumb" role="img" aria-label="Photo of a young boy using a tablet" style="background:linear-gradient(135deg,#eee3d6,#c8a98a)"></div>
  </section>
  <section class="audience" style="left:599px">
    <h3>TWEENS</h3>
    <div class="thumb" role="img" aria-label="Photo of a girl working at a computer" style="background:linear-gradient(135deg,#9a86b8,#5a3f3a)"></div>
  </section>
  <section class="audience" style="left:874px">
    <h3>TEENS</h3>
    <div class="thumb" role="img" aria-label="Photo of teenagers at computers in a classroom" style="background:linear-gradient(135deg,#d9a88b,#5b3a30)"></div>
  </section>
</body>
</html>
```